Designer Instructions – Updated Referral Program Flyer

(Based on the mock-up in “Brief Layout and Instructions.pdf”)

OVERALL STYLE + LAYOUT

Maintain the same general layout, structure, and flow as the mock-up flyer (front and back).

This is an update of an older flyer, not a full redesign — keep the same sections, proportions, and overall visual feel, but with cleaner, more modern design improvements.

The final flyer should look clean, bold, professional, and high-impact, geared toward realtors, property managers, and contractors who refer work.

FRONT SIDE INSTRUCTIONS
1. Header Section

Remove the Rebuild Harbor Crest logo from the top banner.
(Shown on page 1 of the PDF)

2. Main Headline

Keep the same three-line structure:
EARN
UNLIMITED
CASH

Center it, maximize impact, and increase the font size of CASH so all three words match in importance.

Make the headline bold, clean, and the main focal point.

3. Cash Incentive Box

Keep the "$500 minimum OR 10% per referral" box, but upgrade the graphics to look sharper and more modern.

Ensure the wording matches exactly what’s in the mock-up.

4. Premier Partner Program Ribbon

Clean up and modernize the "PREMIER PARTNER PROGRAM" bar while keeping the same position and structure.

Ensure the checkmark badge remains crisp and professional.

5. Supporting Icons Section

Keep the four icons/benefit boxes (Guaranteed Payout, Free Evaluations, Affordable Solutions, Industry Leaders) in the same order.

Update the icons to cleaner, more modern styles — but maintain the same meanings.

Improve alignment and spacing for sharper visual consistency.

6. Remove Icons in Contact Area

At the bottom (“CALL TEXT OR BOOK ONLINE 858-471-6093 BrightlaneRenovate.com”), remove the phone and internet icons, as noted on page 2 of the PDF.

7. Replace All Images

I (Dorian) will provide all updated stock images separately via email.

Replace the flood/water-damage imagery and roof leak with the new images I send.

Keep image placement and proportions the same as the mock-up.

BACK SIDE INSTRUCTIONS
1. Header Image + “REFER / EARN” Section

Maintain the same large split-image layout (“The more you refer, the more you earn”).

Replace all background imagery with the new assets I will send.

Keep the CASH FLOW image section but modernize the type and spacing.

2. “HOW IT WORKS” Section

Preserve the three-column layout:

Refer Flood, Water & Mold Damage

We Take Care of Everything (evaluations/insurance)

Get Paid to Share

Update images, tighten spacing, and use modern iconography.

3. Remove Phone/Internet Icons

Same as the front side — remove small communication icons and keep only the text/number/URL.

4. Bottom Contact Bar

Keep the blue bar, same wording, same layout — just modernize the style if needed for clarity.

5. Replace All Back-Side Images

Again, I will email you the image assets.

Keep the layout EXACT — just update with higher-quality photos and improved design.

TEXT CONTENT (Keep as-is unless spacing adjustments needed)

All text shown in the PDF should remain exactly the same unless spacing or visual balance requires minor adjustments.
Example from page 3:

“REFER FLOOD, MOLD & CONSTRUCTION JOBS”

“We Schedule a Free Estimate. If Approved, You Get Paid.”

“Everybody Benefits From Referrals”

Everything stays, just refreshed and visually improved.

DESIGN GOALS

Flyer should look high-end and trustworthy, not salesy.

Consistent color theme: blues, whites, yellows, same palette as original.

Use bold, modern fonts with strong readability.

Ensure all headlines pop and all benefit boxes are clean, well-aligned, and evenly spaced.

The final result should feel like a premium referral program flyer for a top-tier restoration/remodel company.

FILES I WILL PROVIDE

I will send the designer:

All replacement stock photos

Any updated logos (if needed)

Original high-resolution version of the mock-up (if available)

Any additional icons preferred

Colors
0054AA
0677BA
7BADD7
CADEEF
E8F1F8

Requirements
Must have
• Designer Instructions – Updated Referral Program Flyer (Based on the mock-up in “Brief Layout and Instructions.pdf”) OVERALL STYLE + LAYOUT Maintain the same general layout, structure, and flow as the mock-up flyer (front and back). This is an update of an older flyer, not a full redesign — keep the same sections, proportions, and overall visual feel, but with cleaner, more modern design improvements. The final flyer should look clean, bold, professional, and high-impact, geared toward realtors, property managers, and contractors who refer work. FRONT SIDE INSTRUCTIONS 1. Header Section Remove the Rebuild Harbor Crest logo from the top banner. (Shown on page 1 of the PDF) 2. Main Headline Keep the same three-line structure: EARN UNLIMITED CASH Center it, maximize impact, and increase the font size of CASH so all three words match in importance. Make the headline bold, clean, and the main focal point. 3. Cash Incentive Box Keep the "$500 minimum OR 10% per referral" box, but upgrade the graphics to look sharper and more modern. Ensure the wording matches exactly what’s in the mock-up. 4. Premier Partner Program Ribbon Clean up and modernize the "PREMIER PARTNER PROGRAM" bar while keeping the same position and structure. Ensure the checkmark badge remains crisp and professional. 5. Supporting Icons Section Keep the four icons/benefit boxes (Guaranteed Payout, Free Evaluations, Affordable Solutions, Industry Leaders) in the same order. Update the icons to cleaner, more modern styles — but maintain the same meanings. Improve alignment and spacing for sharper visual consistency. 6. Remove Icons in Contact Area At the bottom (“CALL TEXT OR BOOK ONLINE 858-471-6093 BrightlaneRenovate.com”), remove the phone and internet icons, as noted on page 2 of the PDF. 7. Replace All Images I (Dorian) will provide all updated stock images separately via email. Replace the flood/water-damage imagery and roof leak with the new images I send. Keep image placement and proportions the same as the mock-up. BACK SIDE INSTRUCTIONS 1. Header Image + “REFER / EARN” Section Maintain the same large split-image layout (“The more you refer, the more you earn”). Replace all background imagery with the new assets I will send. Keep the CASH FLOW image section but modernize the type and spacing. 2. “HOW IT WORKS” Section Preserve the three-column layout: Refer Flood, Water & Mold Damage We Take Care of Everything (evaluations/insurance) Get Paid to Share Update images, tighten spacing, and use modern iconography. 3. Remove Phone/Internet Icons Same as the front side — remove small communication icons and keep only the text/number/URL. 4. Bottom Contact Bar Keep the blue bar, same wording, same layout — just modernize the style if needed for clarity. 5. Replace All Back-Side Images Again, I will email you the image assets. Keep the layout EXACT — just update with higher-quality photos and improved design. TEXT CONTENT (Keep as-is unless spacing adjustments needed) All text shown in the PDF should remain exactly the same unless spacing or visual balance requires minor adjustments. Example from page 3: “REFER FLOOD, MOLD & CONSTRUCTION JOBS” “We Schedule a Free Estimate. If Approved, You Get Paid.” “Everybody Benefits From Referrals” Everything stays, just refreshed and visually improved. DESIGN GOALS Flyer should look high-end and trustworthy, not salesy. Consistent color theme: blues, whites, yellows, same palette as original. Use bold, modern fonts with strong readability. Ensure all headlines pop and all benefit boxes are clean, well-aligned, and evenly spaced. The final result should feel like a premium referral program flyer for a top-tier restoration/remodel company. FILES I WILL PROVIDE I will send the designer: All replacement stock photos Any updated logos (if needed) Original high-resolution version of the mock-up (if available) Any additional icons preferred

```html
<!DOCTYPE html>
<html lang="en">
<head>
<meta charset="utf-8">
<title>Referral Program Flyer – Front and Back</title>
<link rel="stylesheet" href="https://fonts.googleapis.com/css2?family=Poppins:wght@500;600;700;800&family=Oswald:wght@600;700&family=Mulish:wght@400;500&display=swap">
<style>
  :root {
    --stage: #8f8f8f;
    --navy: #14296a;
    --royal: #0f3d91;
    --blue: #1a3fa6;
    --deep: #0c2340;
    --yellow: #ffd200;
    --amber: #f4a414;
    --red: #c8171e;
    --slate: #6a7b8b;
    --white: #ffffff;
    --ink: #1d1d1d;
    --sky: #7badd7;
    --mist: #cadeef;
  }
  * { box-sizing: border-box; margin: 0; padding: 0; }
  html, body { width: 1200px; height: 439px; overflow: hidden; }
  body { background: var(--stage); position: relative; font-family: "Poppins", sans-serif; }

  .flyer { position: absolute; top: 47px; width: 534px; height: 345px; background: var(--white); overflow: hidden; }
  .flyer--front { left: 47px; }
  .flyer--back { left: 619px; }
  .abs { position: absolute; }

  /* Front header */
  .front-header { left: 0; top: 0; width: 534px; height: 145px; }
  .headline { left: 0; top: 4px; width: 285px; text-align: center; font-weight: 800; color: var(--white); line-height: 1; }
  .headline span { display: block; }
  .headline .earn { color: var(--yellow); font-size: 40px; }
  .headline .unlimited { font-size: 35px; margin-top: 1px; }
  .headline .cash { font-size: 42px; margin-top: 0; }
  .tagline { left: 27px; top: 117px; width: 304px; height: 26px; background: var(--yellow); color: var(--navy);
    font-weight: 700; font-size: 17.5px; line-height: 26px; padding-left: 19px; white-space: nowrap; }

  .premier-label { left: 350px; top: 150px; width: 60px; text-align: center; font-size: 8px; font-weight: 600; letter-spacing: 1.2px; color: var(--ink); }

  .pill { height: 34px; border-radius: 7px; background: var(--red); color: var(--white); font-weight: 700; }
  .pill-min { left: 30px; top: 164px; width: 78px; }
  .pill-min .amount { position: absolute; left: 12px; top: 2px; font-size: 16px; line-height: 1; }
  .pill-min .unit { position: absolute; left: 7px; top: 20px; font-size: 10px; line-height: 1; }
  .or-badge { left: 95px; top: 170px; width: 25px; height: 25px; border-radius: 50%; background: var(--yellow);
    border: 2px solid var(--white); color: var(--navy); font-size: 9.5px; font-weight: 800; text-align: center; line-height: 21px; }
  .pill-pct { left: 111px; top: 164px; width: 137px; }
  .pill-pct .amount { position: absolute; left: 18px; top: 3px; font-size: 25px; line-height: 1; }
  .pill-pct .unit { position: absolute; left: 73px; top: 5px; font-size: 9.5px; line-height: 1.2; }

  .partner-bar { left: 265px; top: 164px; width: 238px; height: 34px; border-radius: 8px; overflow: hidden; background: var(--slate); }
  .partner-bar .red { position: absolute; left: 0; top: 0; width: 116px; height: 34px; background: var(--red); }
  .partner-bar .word { position: absolute; top: 7px; color: var(--white); font-weight: 600; font-size: 16px; line-height: 1.2; letter-spacing: .3px; }
  .partner-seal { left: 364px; top: 164px; width: 34px; height: 34px; }

  .wins { left: 0; top: 205px; width: 534px; text-align: center; color: var(--blue); font-weight: 700; font-size: 15px; letter-spacing: .2px; }

  .benefit { top: 231px; width: 124px; }
  .benefit .icon { position: absolute; left: 0; top: 0; width: 31px; height: 31px; }
  .benefit .title { position: absolute; left: 35px; top: 5px; font-size: 8.4px; font-weight: 700; color: var(--navy); line-height: 1.35; letter-spacing: .2px; }
  .benefit .desc { position: absolute; left: 2px; top: 37px; width: 130px; font-family: "Mulish", sans-serif; font-size: 7.6px; color: var(--ink); line-height: 1.4; }

  .grow { left: 0; top: 297px; width: 534px; text-align: center; font-weight: 700; font-size: 12.6px; color: var(--navy); }
  .grow em { font-style: normal; color: var(--red); }

  .contact-bar { left: 0; width: 534px; height: 28px; }
  .contact-bar .cta { position: absolute; left: 19px; top: 6px; color: var(--white); font-weight: 700; font-size: 11.8px; letter-spacing: .2px; white-space: nowrap; }
  .contact-bar .cta small { font-weight: 500; font-size: 11.8px; }
  .contact-bar .details { position: absolute; top: 5px; color: var(--navy); font-weight: 700; font-size: 12.8px; white-space: nowrap; letter-spacing: .2px; }
  .contact-bar .details .sep { display: inline-block; width: 1px; height: 14px; background: var(--navy); margin: 0 5px -2px; }

  /* Back */
  .refer-stack { left: 0; top: 16px; width: 282px; text-align: center; font-family: "Oswald", sans-serif; font-weight: 700; line-height: 1; }
  .refer-stack .small { display: block; color: var(--white); font-size: 18px; letter-spacing: -.2px; }
  .refer-stack .big { display: block; font-size: 44px; letter-spacing: -.5px;
    background: linear-gradient(180deg, var(--yellow) 0%, var(--amber) 100%); -webkit-background-clip: text; background-clip: text; color: transparent; }
  .how-tab { left: 14px; top: 140px; width: 154px; height: 17px; }
  .how-tab span { position: absolute; left: 24px; top: 0; font-weight: 700; font-size: 12.8px; color: var(--navy); line-height: 17px; letter-spacing: .3px; }

  .step { top: 164px; width: 138px; height: 142px; background: var(--white); border-radius: 6px; box-shadow: 0 1px 5px rgba(0,0,0,.18); }
  .step .photo { position: absolute; left: 7px; top: 7px; width: 124px; height: 72px; border-radius: 5px; }
  .step .title { position: absolute; left: 0; top: 85px; width: 138px; text-align: center; font-size: 8.4px; font-weight: 700; color: var(--ink); line-height: 1.45; }
  .step .desc { position: absolute; left: 0; top: 112px; width: 138px; text-align: center; font-family: "Mulish", sans-serif; font-size: 7.6px; color: var(--ink); line-height: 1.62; }
</style>
</head>
<body>

<!-- FRONT -->
<section class="flyer flyer--front" aria-label="Referral flyer front">
  <svg class="abs front-header" viewBox="0 0 534 145" aria-hidden="true">
    <defs>
      <linearGradient id="frontBlue" x1="0" y1="0" x2="1" y2="1">
        <stop offset="0" stop-color="#163f95"/><stop offset="1" stop-color="#0e2f74"/>
      </linearGradient>
    </defs>
    <rect width="534" height="145" fill="url(#frontBlue)"/>
    <polygon points="317,0 534,0 534,145 300,145 275,72" fill="#ffffff"/>
  </svg>
  <div class="abs" role="img" aria-label="City skyline at dusk with lit towers over the waterfront"
       style="left:0;top:0;width:534px;height:145px;clip-path:polygon(321px 0,534px 0,534px 145px,305px 145px,280px 72px);background:linear-gradient(180deg,#7a6aa8 0%,#a77fa6 35%,#6b4a5c 62%,#3a2a2e 100%);"></div>

  <h1 class="abs headline"><span class="earn">EARN</span><span class="unlimited">UNLIMITED</span><span class="cash">CASH</span></h1>
  <div class="abs tagline">GET PAID TOREFER A FLOOD</div>

  <div class="abs premier-label">PREMIEM</div>

  <div class="abs pill pill-min"><span class="amount">$500</span><span class="unit">MINIMUM</span></div>
  <div class="abs pill pill-pct"><span class="amount">10%</span><span class="unit">PER<br>REFERRAL!</span></div>
  <div class="abs or-badge">OR</div>

  <div class="abs partner-bar">
    <div class="red"></div>
    <span class="word" style="left:14px;">PARTNER</span>
    <span class="word" style="left:148px;">PROGRAM</span>
  </div>
  <svg class="abs partner-seal" viewBox="0 0 34 34" aria-hidden="true">
    <polygon points="17,0 21,4 27,3 28,9 33,12 31,17 33,22 28,25 27,31 21,30 17,34 13,30 7,31 6,25 1,22 3,17 1,12 6,9 7,3 13,4" fill="#ffd200"/>
    <circle cx="17" cy="17" r="9.5" fill="none" stroke="#14296a" stroke-width="2"/>
    <polyline points="12.5,17 16,20.5 22,13.5" fill="none" stroke="#14296a" stroke-width="2.4" stroke-linecap="round" stroke-linejoin="round"/>
  </svg>

  <h2 class="abs wins">PARTNER WITH US &amp; EVERYBODY WINS!</h2>

  <div class="abs benefit" style="left:23px;">
    <svg class="icon" viewBox="0 0 31 31" aria-hidden="true"><circle cx="15.5" cy="15.5" r="14.3" fill="#fff" stroke="#14296a" stroke-width="1.6"/><circle cx="16" cy="13" r="6" fill="#14296a"/><text x="16" y="16" font-size="8" font-weight="700" fill="#ffd200" text-anchor="middle" font-family="Poppins, sans-serif">$</text><path d="M7 21 h8 l5 -2 h4 v3 l-8 3 h-9z" fill="#14296a"/></svg>
    <div class="title">GUARANTEED<br>PAYOUT*</div>
    <div class="desc">Minimum $500 or 10% of<br>Total Invoice Paid Fast</div>
  </div>
  <div class="abs benefit" style="left:150px;">
    <svg class="icon" viewBox="0 0 31 31" aria-hidden="true"><circle cx="15.5" cy="15.5" r="14.3" fill="#fff" stroke="#14296a" stroke-width="1.6"/><rect x="9.5" y="8" width="11" height="14" rx="1" fill="none" stroke="#14296a" stroke-width="1.5"/><line x1="12" y1="13" x2="18" y2="13" stroke="#14296a" stroke-width="1.2"/><line x1="12" y1="16" x2="18" y2="16" stroke="#14296a" stroke-width="1.2"/><circle cx="20" cy="21" r="3.2" fill="#ffd200"/></svg>
    <div class="title">FREE<br>ESTIMATES</div>
    <div class="desc">Fast &amp; Free Inspections &amp;<br>Written Estimates</div>
  </div>
  <div class="abs benefit" style="left:277px;">
    <svg class="icon" viewBox="0 0 31 31" aria-hidden="true"><circle cx="15.5" cy="15.5" r="14.3" fill="#fff" stroke="#14296a" stroke-width="1.6"/><circle cx="12.5" cy="12" r="3.2" fill="#14296a"/><path d="M7 22 a5.5 5.5 0 0 1 11 0z" fill="#14296a"/><rect x="18" y="10" width="6" height="6" rx="1" fill="#ffd200"/><rect x="18" y="17" width="6" height="5" rx="1" fill="#ffd200"/></svg>
    <div class="title">AFFORDABLE<br>SOLUTIONS</div>
    <div class="desc">Lowest Out of Pocket<br>Costs for Your Customers</div>
  </div>
  <div class="abs benefit" style="left:399px;">
    <svg class="icon" viewBox="0 0 31 31" aria-hidden="true"><circle cx="15.5" cy="15.5" r="14.3" fill="#fff" stroke="#14296a" stroke-width="1.6"/><circle cx="15.5" cy="9.5" r="2.6" fill="#ffd200"/><circle cx="15.5" cy="17" r="3" fill="#14296a"/><path d="M8 16 l3 6 h9 l3 -6 l-4 3 h-7z" fill="#14296a"/></svg>
    <div class="title">INDUSTRY<br>LEADERS</div>
    <div class="desc">Licensed &amp; Certified Experts<br>Provide 100% Guarantee</div>
  </div>

  <p class="abs grow">SEND <em>REFERRALS</em>. GET <em>PAID</em>. GROW <em>YOUR BUSINESS.</em></p>

  <div class="abs contact-bar" style="top:322px;height:23px;">
    <svg class="abs" style="left:0;top:0;" width="230" height="23" viewBox="0 0 230 23" aria-hidden="true"><polygon points="0,0 207,0 217,23 0,23" fill="#14296a"/></svg>
    <div class="cta" style="top:4px;">CALL TEXT <small>OR</small> BOOK ON-LINE</div>
    <div class="details" style="left:227px;top:3px;">858-471-6093<span class="sep"></span>www.BrightlaneRenovate.com</div>
  </div>
</section>

<!-- BACK -->
<section class="flyer flyer--back" aria-label="Referral flyer back">
  <svg class="abs" style="left:0;top:0;" width="534" height="154" viewBox="0 0 534 154" aria-hidden="true">
    <rect width="534" height="154" fill="#1455a4"/>
    <polygon points="150,8 258,80 287,154 150,154 100,120" fill="#0c2340"/>
  </svg>
  <div class="abs" role="img" aria-label="Spread of hundred-dollar bills with letter tiles spelling CASH FLOW"
       style="left:0;top:0;width:534px;height:154px;clip-path:polygon(264px 0,534px 0,534px 154px,287px 154px);background:linear-gradient(135deg,#c9cfc4 0%,#e6e6dc 40%,#b7c0b2 70%,#d7dccf 100%);"></div>

  <div class="abs refer-stack">
    <span class="small">THE MORE YOU</span>
    <span class="big">REFER</span>
    <span class="small">THE MORE YOU</span>
    <span class="big">EARN</span>
  </div>

  <div class="abs how-tab">
    <svg class="abs" style="left:0;top:0;" width="154" height="17" viewBox="0 0 154 17" aria-hidden="true"><polygon points="0,0 148,0 154,17 0,17" fill="#ffd200"/></svg>
    <span>HOW IT WORKS</span>
  </div>

  <div class="abs step" style="left:34px;">
    <div class="photo" role="img" aria-label="Drying fans and dehumidifiers set up in a room" style="background:linear-gradient(180deg,#d8d2c6 0%,#9fb3bb 55%,#2f8fc4 100%);"></div>
    <div class="title">REFER FLOOD, MOLD &amp;<br>CONSTRUCTION JOBS</div>
    <div class="desc">It’s Simple to Refer 24/7<br>Call, Text or Book Online.</div>
  </div>
  <div class="abs step" style="left:198px;">
    <div class="photo" role="img" aria-label="Inspector with clipboard in front of a house" style="background:linear-gradient(180deg,#9cc4e4 0%,#e7e7e2 45%,#6f8a5a 100%);"></div>
    <div class="title">WE TAKE CARE OF<br>EVERYTHING</div>
    <div class="desc">We Schedule a Free Estimate.<br>If Approved, You Get Paid.</div>
  </div>
  <div class="abs step" style="left:362px;">
    <div class="photo" role="img" aria-label="Yellow road sign reading GET PAID TO SHARE against a cloudy sky" style="background:linear-gradient(180deg,#3f86cf 0%,#9cc4ea 50%,#e5eef6 100%);"></div>
    <div class="title">EVERYBODY BENEFITS<br>FROM REFERRALS</div>
    <div class="desc">We Provide Expert Quality<br>Work for AAordable Price.</div>
  </div>

  <div class="abs contact-bar" style="top:317px;">
    <svg class="abs" style="left:0;top:0;" width="230" height="28" viewBox="0 0 230 28" aria-hidden="true"><polygon points="0,0 205,0 218,28 0,28" fill="#14296a"/></svg>
    <div class="cta">CALL TEXT <small>OR</small> BOOK ON-LINE</div>
    <div class="details" style="left:227px;top:4px;">858-471-6093<span class="sep"></span>www.BrightlaneRenovate.com</div>
  </div>
</section>

</body>
</html>
```